Residential building / Apartments for sale landing page

I need a website / landing page design for my latest development project - a residential building with 70+ apartments for sale. I need the design in layers in Photoshop/Illustrator/InDesign format with all the icons/shapes/maps/graphic assets in vector format (svg, ai, eps) as much as possible.

I prefer white website and please consider the performance/coding experience. We're not making something suitable only for a design contest with fancy parallax effects and confusing animations. We're trying to create usable and clean UI with good UX.

The website will be custom coded, i.e. I'm not using WordPress.

I know that the existing 3D photos are not good but for now you can use them or replace them with some stock photos. I'm going to create new 3D photos soon.

Real Estate Development

1 page

```html
<!DOCTYPE html>
<html lang="en">
<head>
<meta charset="utf-8">
<title>Verdant Heights – Apartments for Sale</title>
<link href="https://fonts.googleapis.com/css2?family=Oswald:wght@400;500;600;700&family=Lato:wght@400;700&display=swap" rel="stylesheet">
<style>
:root{
  --green:#7ab929;
  --green-dark:#5f9a1c;
  --ink:#1e1e1e;
  --text:#555;
  --muted:#888;
  --line:#e3e3e3;
  --dark:#202020;
  --dark-2:#2a2a2a;
  --white:#fff;
}
*{box-sizing:border-box;margin:0;padding:0}
html,body{width:1200px;height:5200px;overflow:hidden}
body{font-family:"Lato",Arial,sans-serif;color:var(--text);background:var(--white);font-size:15px;line-height:1.6}
h1,h2,h3,h4,.brand,.btn,.nav a{font-family:"Oswald","Arial Narrow",sans-serif}
.btn{display:inline-block;background:var(--green);color:var(--white);font-size:15px;font-weight:500;letter-spacing:1px;padding:12px 30px;text-transform:uppercase;text-decoration:none}
.btn-outline{background:transparent;border:2px solid var(--white)}
.section-title{text-align:center}
.section-title .mark{width:44px;height:44px;background:var(--green);border-radius:50%;margin:0 auto 14px}
.section-title h2{font-size:40px;font-weight:600;color:var(--ink);text-transform:uppercase;line-height:1.1}
.section-title p{font-size:15px;color:var(--text);margin-top:6px}
.ph{display:block}

/* header */
.site-header{position:relative;height:96px;background:var(--white)}
.brand{position:absolute;left:112px;top:8px;font-size:30px;font-weight:700;color:var(--ink);text-transform:uppercase;display:flex;align-items:center;gap:10px;line-height:1}
.brand .dot{width:22px;height:22px;background:var(--green)}
.topbar{position:absolute;right:80px;top:10px;display:flex;align-items:center;gap:16px;font-size:13px;color:var(--ink)}
.topbar .soc{width:22px;height:22px;background:var(--green);border-radius:3px}
.nav{position:absolute;left:464px;right:80px;top:56px;height:40px;background:var(--green);display:flex;justify-content:flex-end;align-items:center;gap:30px;padding-right:24px}
.nav a{color:var(--white);font-size:15px;text-decoration:none}

/* hero */
.hero{position:relative;height:664px;background:linear-gradient(180deg,#8fb3d6 0%,#a9c3d8 30%,#7e8f74 60%,#4a5b3a 100%)}
.hero-copy{position:absolute;left:0;right:0;top:220px;text-align:center;color:var(--white)}
.hero-copy h1{font-size:34px;font-weight:500;line-height:1.35;text-transform:uppercase;letter-spacing:1px}
.hero-copy .btn{margin-top:30px;padding:12px 40px}

/* project */
.project{height:490px;position:relative}
.project .ph{position:absolute;left:112px;top:30px;width:468px;height:330px;background:linear-gradient(160deg,#e9eef2,#b9c7b0 60%,#6f8f4e)}
.project-copy{position:absolute;left:632px;top:80px;width:460px}
.project-copy .bar{width:44px;height:4px;background:var(--green);margin-bottom:16px}
.project-copy h2{font-size:36px;font-weight:600;color:var(--ink);text-transform:uppercase;line-height:1.1}
.project-copy p{margin:18px 0 26px;font-size:14px;line-height:1.75}

/* facilities */
.facilities{height:1080px;position:relative;padding-top:40px}
.facilities .ph{position:absolute;left:112px;top:198px;width:976px;height:472px;background:linear-gradient(170deg,#dfe9f1 0%,#b6c7a5 50%,#5e7d45 100%)}
.cards{position:absolute;left:112px;top:670px;width:976px;height:260px;display:grid;grid-template-columns:repeat(4,1fr);gap:8px;background:var(--white)}
.card{border:1px solid var(--line);text-align:center;padding:28px 20px}
.card svg{display:block;margin:0 auto 10px}
.card h3{font-family:"Lato",sans-serif;font-size:17px;font-weight:700;color:var(--ink)}
.card p{font-size:12px;line-height:1.6;margin:8px 0 10px}
.card a,.more{color:var(--green);font-size:14px;font-weight:700;text-decoration:none}
.arrow{position:absolute;top:784px;width:20px;height:30px}
.arrow.l{left:70px}.arrow.r{right:70px}
.facilities .view{position:absolute;left:0;right:0;top:960px;text-align:center}

/* construction */
.construction{height:660px;display:flex;background:var(--dark)}
.construction .ph{width:600px;height:100%;background:linear-gradient(135deg,#5d6b72,#8a9380 50%,#3c4a33)}
.construction-copy{flex:1;padding:110px 90px 0 60px;color:#ddd}
.construction-copy h2{font-size:36px;font-weight:600;color:var(--white);text-transform:uppercase;line-height:1.1}
.construction-copy .sub{font-size:14px;margin:6px 0 26px}
.features{list-style:none}
.features li{display:flex;gap:14px;font-size:13px;line-height:1.6;margin-bottom:16px}
.features li svg{flex:none;margin-top:2px}
.construction-copy .btn{margin-top:16px}

/* location */
.location{height:650px;position:relative;padding-top:70px}
.location .section-title p{max-width:640px;margin:6px auto 0;font-size:14px}
.location .ph{position:absolute;left:0;top:300px;width:1200px;height:340px;background:linear-gradient(135deg,#eceef0,#dfe3e6 50%,#e8ebe6)}

/* gallery */
.gallery{height:660px;position:relative;padding-top:50px}
.gallery-grid{position:absolute;left:112px;top:236px;width:976px;display:grid;grid-template-columns:repeat(3,1fr);gap:30px;text-align:center}
.gallery-grid .ph{height:300px;background:linear-gradient(160deg,#f4f4f4,#dcdcdc)}
.gallery-grid h3{font-size:30px;font-weight:500;color:var(--ink);margin-top:40px;line-height:1.2}

/* contact */
.contact{height:660px;background:var(--dark);color:#ddd;position:relative;padding-top:72px}
.contact .section-title h2{color:var(--white)}
.contact .section-title p{color:#ccc;font-size:14px;margin-top:2px}
.form{position:absolute;left:144px;top:238px;width:576px;display:grid;grid-template-columns:1fr 1fr;gap:12px}
.field{background:var(--white);height:40px;font-size:12px;color:var(--muted);padding:10px 12px}
.field.full{grid-column:1/3}
.field.msg{height:100px}
.form .btn{grid-column:1/2;justify-self:start;margin-top:10px;padding:11px 44px}
.details{position:absolute;left:780px;top:250px;width:300px}
.detail{display:flex;gap:18px;margin-bottom:20px}
.detail .ico{width:40px;height:40px;border-radius:50%;background:var(--green);flex:none;display:flex;align-items:center;justify-content:center}
.detail h4{font-family:"Lato",sans-serif;font-size:15px;color:var(--white);font-weight:700}
.detail p{font-size:14px;line-height:1.5}
.socials{display:flex;gap:12px;margin-top:16px;margin-left:36px}
.socials span{width:36px;height:36px;border:2px solid #ccc;border-radius:50%}

/* footer */
.site-footer{height:240px;text-align:center;padding-top:46px}
.site-footer .brand{position:static;justify-content:center;font-size:34px}
.footer-nav{margin-top:36px;font-family:"Oswald",sans-serif;font-size:16px;color:var(--ink);font-weight:500;letter-spacing:.5px}
.footer-nav span{margin:0 14px}
.copyright{font-size:13px;color:var(--text);margin-top:10px}
</style>
</head>
<body>

<header class="site-header">
  <div class="brand"><span class="dot"></span>Verdant Heights</div>
  <div class="topbar">
    <span>CONTACT</span><span>|</span><span>English ▾</span>
    <span class="soc"></span><span class="soc"></span><span class="soc"></span>
  </div>
  <nav class="nav">
    <a>Home</a><a>Verdant Heights</a><a>The project</a><a>Apartment Sales</a><a>Location</a><a>Gallery</a>
  </nav>
</header>

<section class="hero" role="img" aria-label="Rendering of a white residential tower covered with greenery on its balconies">
  <div class="hero-copy">
    <h1>Sale of apartments directly from the investor<br>with 10% discount price from XXX EUR/M2</h1>
    <a class="btn">Buy</a>
  </div>
</section>

<section class="project">
  <div class="ph" role="img" aria-label="Rendering of the green apartment building seen from a corner"></div>
  <div class="project-copy">
    <div class="bar"></div>
    <h2>Project Presentation</h2>
    <p>Lorem ipsum dolor sit amet, consectetur adipiscing elit, sed do eiusmod tempor incididunt ut labore et dolore magna aliqua. Ut enim ad minim veniam, quis nostrud exercitation ullamco laboris nisi ut aliquip ex ea commodo consequat. Duis aute irure dolor in reprehenderit in voluptate velit esse cillum dolore eu fugiat nulla pariatur. Excepteur sint occaecat cupidatat non proident, sunt in culpa qui officia deserunt mollit anim id est laborum.</p>
    <a class="btn">Read more</a>
  </div>
</section>

<section class="facilities">
  <div class="section-title">
    <div class="mark"></div>
    <h2>Our Facilities</h2>
    <p>Lorem ipsum dolor sit amet, consectetur adipiscing</p>
  </div>
  <div class="ph" role="img" aria-label="Rendering of the building facade with terraces full of plants"></div>
  <svg class="arrow l" viewBox="0 0 20 30"><path d="M15 4 5 15l10 11" fill="none" stroke="#999" stroke-width="2"/></svg>
  <svg class="arrow r" viewBox="0 0 20 30"><path d="M5 4l10 11L5 26" fill="none" stroke="#999" stroke-width="2"/></svg>
  <div class="cards">
    <div class="card">
      <svg width="48" height="40" viewBox="0 0 48 40" fill="none" stroke="#7ab929" stroke-width="2"><circle cx="16" cy="14" r="9"/><path d="M16 23v14M32 16l8 10H24zM32 26v11M4 37h40"/></svg>
      <h3>Green areas &amp; gardens</h3>
      <p>Lorem ipsum dolor sit amet, consectetur adipiscing elit, sed do eiusmod tempor incididunt ut labore et dolore</p>
      <a>Read More &gt;</a>
    </div>
    <div class="card">
      <svg width="48" height="40" viewBox="0 0 48 40" fill="none" stroke="#7ab929" stroke-width="2"><rect x="6" y="4" width="36" height="32" rx="3"/><path d="M18 30V10h8a6 6 0 0 1 0 12h-8"/></svg>
      <h3>Parking spaces</h3>
      <p>Lorem ipsum dolor sit amet, consectetur adipiscing elit, sed do eiusmod tempor incididunt ut labore et dolore</p>
      <a>Read More &gt;</a>
    </div>
    <div class="card">
      <svg width="48" height="40" viewBox="0 0 48 40" fill="none" stroke="#7ab929" stroke-width="2"><circle cx="11" cy="27" r="8"/><circle cx="37" cy="27" r="8"/><path d="M11 27l8-14h12l6 14M19 13l6 14h6"/></svg>
      <h3>Bicycle parking</h3>
      <p>Lorem ipsum dolor sit amet, consectetur adipiscing elit, sed do eiusmod tempor incididunt ut labore et dolore</p>
      <a>Read More &gt;</a>
    </div>
    <div class="card">
      <svg width="48" height="40" viewBox="0 0 48 40" fill="none" stroke="#7ab929" stroke-width="2"><path d="M6 20h36M10 12v16M14 14v12M38 12v16M34 14v12"/></svg>
      <h3>Outside workout area</h3>
      <p>Lorem ipsum dolor sit amet, consectetur adipiscing elit, sed do eiusmod tempor incididunt ut labore et dolore</p>
      <a>Read More &gt;</a>
    </div>
  </div>
  <div class="view"><a class="btn">View all</a></div>
</section>

<section class="construction">
  <div class="ph" role="img" aria-label="Aerial rendering of the building with solar panels on the roof"></div>
  <div class="construction-copy">
    <h2>Construction Features</h2>
    <p class="sub">Lorem ipsum dolor sit amet, consectetur adipiscing</p>
    <ul class="features">
      <li><svg width="16" height="16" viewBox="0 0 16 16"><circle cx="8" cy="8" r="8" fill="#ddd"/><path d="M4.5 8.2l2.3 2.3 4.7-4.8" fill="none" stroke="#202020" stroke-width="1.8"/></svg><span>Altura Windows - 5 chamber noise reducing glazing with high temperature and noise insulation efficiency</span></li>
      <li><svg width="16" height="16" viewBox="0 0 16 16"><circle cx="8" cy="8" r="8" fill="#ddd"/><path d="M4.5 8.2l2.3 2.3 4.7-4.8" fill="none" stroke="#202020" stroke-width="1.8"/></svg><span>Korvell bricks - Thermacore clay bricks with porous system and 25 cm thick outer walls</span></li>
      <li><svg width="16" height="16" viewBox="0 0 16 16"><circle cx="8" cy="8" r="8" fill="#ddd"/><path d="M4.5 8.2l2.3 2.3 4.7-4.8" fill="none" stroke="#202020" stroke-width="1.8"/></svg><span>High Ceilings - 2.70m high ceilings giving the light and space you need</span></li>
      <li><svg width="16" height="16" viewBox="0 0 16 16"><circle cx="8" cy="8" r="8" fill="#ddd"/><path d="M4.5 8.2l2.3 2.3 4.7-4.8" fill="none" stroke="#202020" stroke-width="1.8"/></svg><span>Thermal Insulation System Silvane - Silicone Plaster Thermal Insulation System 10 cm thick and 15 cm thick from the north walls</span></li>
    </ul>
    <a class="btn btn-outline">Read more</a>
  </div>
</section>

<section class="location">
  <div class="section-title">
    <div class="mark"></div>
    <h2>Our Location</h2>
    <p>Sed ut perspiciatis unde omnis iste natus error sit voluptatem accusantium doloremque<br>illo inventore veritatis et quasi architecto beatae.</p>
  </div>
  <div class="ph" role="img" aria-label="Street map of the neighbourhood around the building"></div>
</section>

<section class="gallery">
  <div class="section-title">
    <div class="mark"></div>
    <h2>Our Gallery</h2>
    <p>Lorem ipsum dolor sit amet, consectetur adipiscing</p>
  </div>
  <div class="gallery-grid">
    <div><div class="ph" role="img" aria-label="Coloured apartment floor plan"></div><h3>April 2021</h3><a class="more">Read More &gt;</a></div>
    <div><div class="ph" role="img" aria-label="Architectural floor plan drawing"></div><h3>March 2021</h3><a class="more">Read More &gt;</a></div>
    <div><div class="ph" role="img" aria-label="Site plan drawing of the building"></div><h3>February 2021</h3><a class="more">Read More &gt;</a></div>
  </div>
</section>

<section class="contact">
  <div class="section-title">
    <h2>Contact Us</h2>
    <p style="margin-top:14px">Sed ut perspiciatis unde omnis iste natus error sit voluptatem accusantium doloremque</p>
    <p>illo inventore veritatis et quasi architecto beatae.</p>
  </div>
  <div class="form">
    <div class="field">First Name</div><div class="field">Last Name</div>
    <div class="field full">Email Address</div>
    <div class="field">City</div><div class="field">Phone Number</div>
    <div class="field full msg">Message</div>
    <a class="btn">Submit</a>
  </div>
  <div class="details">
    <div class="detail">
      <span class="ico"><svg width="18" height="22" viewBox="0 0 18 22"><path d="M9 1a7 7 0 0 0-7 7c0 5 7 13 7 13s7-8 7-13a7 7 0 0 0-7-7z" fill="#fff"/><circle cx="9" cy="8" r="2.6" fill="#7ab929"/></svg></span>
      <div><h4>Address:</h4><p>123 Avenue name, City name<br>10100, United States</p></div>
    </div>
    <div class="detail">
      <span class="ico"><svg width="18" height="18" viewBox="0 0 18 18"><path d="M4 1l3 4-2 2c1 2.5 3.5 5 6 6l2-2 4 3-2 3C8 17 1 10 1 3z" fill="#fff"/></svg></span>
      <div><h4>Phone:</h4><p>+888 888 8888</p></div>
    </div>
    <div class="detail">
      <span class="ico"><svg width="20" height="14" viewBox="0 0 20 14"><rect x="1" y="1" width="18" height="12" fill="#fff"/><path d="M1 1l9 7 9-7" fill="none" stroke="#7ab929" stroke-width="1.5"/></svg></span>
      <div><h4>Email:</h4><p>info@verdantheights.example</p></div>
    </div>
    <div class="socials"><span></span><span></span><span></span><span></span></div>
  </div>
</section>

<footer class="site-footer">
  <div class="brand"><span class="dot"></span>Verdant Heights</div>
  <div class="footer-nav">VERDANT HEIGHTS<span>|</span>THE PROJECT<span>|</span>APARTMENTS/SALES<span>|</span>LOCATION<span>|</span>GALLERY</div>
  <p class="copyright">Copyright 2021 Verdant Heights. All rights reserved.</p>
</footer>

</body>
</html>
```